Heron Loan Partners Business Card

We need a business card design for our mortgage servicing company. In addition to servicing the loans of homeowners, we help homeowners with purchasing their homes and any mortgage refinancing. We would like to see designs that use the colors in the logo attached below (gold-ish yellow and navy blue), and any other design you deem fit! The design should communicate a simpler life with smart mortgages provided by Heron.

```html
<!DOCTYPE html>
<html lang="en">
<head>
<meta charset="utf-8">
<title>Heron Loan Partners Business Card</title>
<link href="https://fonts.googleapis.com/css2?family=Open+Sans:wght@400;600;700&display=swap" rel="stylesheet">
<style>
  :root {
    --navy: #241f5c;
    --gold: #d9a93c;
    --card-front: #f4f4f4;
    --card-back: #ffffff;
    --ink: #1c1c1c;
    --stage: #232323;
  }
  * { box-sizing: border-box; margin: 0; padding: 0; }
  html, body {
    width: 1200px; height: 780px; overflow: hidden;
    background: var(--stage);
    font-family: "Open Sans", Arial, sans-serif;
  }
  .stage {
    position: relative; width: 1200px; height: 780px;
    display: flex; align-items: center; justify-content: center; gap: 40px;
  }
  .card {
    position: relative; width: 540px; height: 309px; overflow: hidden;
    box-shadow: 0 12px 30px rgba(0,0,0,.45);
  }
  .card--front { background: var(--card-front); }
  .card--back { background: var(--card-back); display: flex; align-items: center; justify-content: center; }

  .card__band { position: absolute; inset: 0; }

  .brand {
    position: absolute; display: flex; align-items: center; gap: 10px;
    color: var(--navy); font-weight: 700; white-space: nowrap;
  }
  .brand__dot { border-radius: 50%; background: var(--gold); flex: none; }
  .card--front .brand { left: 250px; top: 62px; font-size: 24px; }
  .card--front .brand__dot { width: 18px; height: 18px; }
  .card--back .brand { position: static; font-size: 40px; gap: 16px; }
  .card--back .brand__dot { width: 30px; height: 30px; }

  .holder { position: absolute; left: 40px; top: 92px; }
  .holder__name { font-size: 22px; font-weight: 700; line-height: 1.1; }
  .holder__first { color: var(--gold); }
  .holder__last { color: var(--navy); }
  .holder__title { font-size: 11.5px; color: var(--ink); margin-top: 3px; margin-left: 22px; }

  .divider { position: absolute; left: 232px; top: 128px; width: 2px; height: 86px; background: var(--ink); }

  .contacts { position: absolute; left: 250px; top: 130px; list-style: none; }
  .contacts__item { display: flex; align-items: center; gap: 8px; font-size: 12.5px; color: var(--ink); height: 20px; }
  .contacts__icon { width: 12px; height: 12px; fill: var(--gold); flex: none; }

  .address {
    position: absolute; left: 30px; top: 262px;
    font-size: 12.5px; color: #fff; white-space: nowrap;
    transform: rotate(6deg); transform-origin: left center;
  }
</style>
</head>
<body>
<main class="stage">
  <section class="card card--front" aria-label="Card front">
    <svg class="card__band" viewBox="0 0 540 309" preserveAspectRatio="none" aria-hidden="true">
      <path d="M0,210 C60,214 70,230 150,250 C280,280 420,290 540,286 L540,309 L0,309 Z" fill="var(--gold)"/>
      <path d="M26,176 C90,240 260,278 520,283" fill="none" stroke="var(--navy)" stroke-width="3" stroke-linecap="round"/>
    </svg>

    <div class="brand"><span class="brand__dot"></span>Heron Loan Partners</div>

    <div class="holder">
      <p class="holder__name"><span class="holder__first">Lena</span> <span class="holder__last">Varga</span></p>
      <p class="holder__title">Managing Director</p>
    </div>

    <div class="divider"></div>

    <ul class="contacts">
      <li class="contacts__item">
        <svg class="contacts__icon" viewBox="0 0 24 24"><path d="M6.6 10.8a15.1 15.1 0 0 0 6.6 6.6l2.2-2.2a1 1 0 0 1 1-.25 11.4 11.4 0 0 0 3.6.57 1 1 0 0 1 1 1V20a1 1 0 0 1-1 1A17 17 0 0 1 3 4a1 1 0 0 1 1-1h3.5a1 1 0 0 1 1 1c0 1.25.2 2.45.57 3.6a1 1 0 0 1-.25 1z"/></svg>
        (555) 214-3087
      </li>
      <li class="contacts__item">
        <svg class="contacts__icon" viewBox="0 0 24 24"><path d="M7 1h10a2 2 0 0 1 2 2v18a2 2 0 0 1-2 2H7a2 2 0 0 1-2-2V3a2 2 0 0 1 2-2zm0 3v14h10V4zm5 15.5a1.2 1.2 0 1 0 0 2.4 1.2 1.2 0 0 0 0-2.4z"/></svg>
        (555) 214-3087
      </li>
      <li class="contacts__item">
        <svg class="contacts__icon" viewBox="0 0 24 24"><path d="M2 5h20v14H2zm2 2v.4l8 5 8-5V7zm0 2.8V17h16V9.8l-8 5z"/></svg>
        hello@heronloan.com
      </li>
      <li class="contacts__item">
        <svg class="contacts__icon" viewBox="0 0 24 24"><path d="M12 2a10 10 0 1 0 0 20 10 10 0 0 0 0-20zm6.9 6h-3a15.6 15.6 0 0 0-1.4-3.6A8 8 0 0 1 18.9 8zM12 4c.8 1.2 1.5 2.5 1.9 4h-3.8c.4-1.5 1.1-2.8 1.9-4zM4.3 14a8 8 0 0 1 0-4h3.4a16 16 0 0 0 0 4zm.8 2h3a15.6 15.6 0 0 0 1.4 3.6A8 8 0 0 1 5.1 16zm3-8h-3a8 8 0 0 1 4.4-3.6A15.6 15.6 0 0 0 8.1 8zM12 20c-.8-1.2-1.5-2.5-1.9-4h3.8c-.4 1.5-1.1 2.8-1.9 4zm2.3-6H9.7a14.5 14.5 0 0 1 0-4h4.6a14.5 14.5 0 0 1 0 4zm.2 5.6a15.6 15.6 0 0 0 1.4-3.6h3a8 8 0 0 1-4.4 3.6zm1.8-5.6a16 16 0 0 0 0-4h3.4a8 8 0 0 1 0 4z"/></svg>
        www.heronloan.com
      </li>
    </ul>

    <p class="address">418 Willow Crest Ave. Suite 120 Denton, TX 76201</p>
  </section>

  <section class="card card--back" aria-label="Card back">
    <div class="brand"><span class="brand__dot"></span>Heron Loan Partners</div>
  </section>
</main>
</body>
</html>
```